Website for a company offering full serivce charging solutions for electric cars

The company "tanu-werk" (english: "tanu-works") offering all-in-one-solutions for charging infrastructure for electric mobility.

There are four products:
1- Wallboxes for single-family homes
2- Solutions for property devloper/-management for property parking space
3- All-in-one-charging solution for municipalities/communities
4- Solutions for tourism/hotels/holiday appartments

The Website structure:
1. Main Page
2.1. Product Page Single Homes
2.2. Product Page Property Management / Parking
2.3. Product Page Municipality
2.4. Product Page Tourism
3. Contact Form / Request for information
4. Imprint / Legal

The Website should be built on Wordpress with a powerful possibility to simply add/modify specific landing pages.

We would like you to implement the website later and also maintain it if possible, but we would be able to do minor modifications by ourselfs (for A/B-Testing)

The website should be clear and simple, easy to understand.
Target group is mainly B2C without deeper knowledge of that topic.

It should suggest, that we will provide a very simple way to get the charging infrastructure done.

We need a contact form, maybe we will use Hubspot later.

Attached you will find a draft of the main page and a landing page (for 2.2) - it is just the content, please ignore the design. We would love to let you create a suitable design.
Also you will find some drafts a bit different for the same story.

I added also a few stock photos, but they don't need to be used! If you have better ideas, you are welcome!

Industry/Entity Type

Charging/Electric mobility

Number of Pages Required

2 page

Font styles to use
Sans Serif

Requirements
Must have
• Based on Wordpress, and the designer should be able to implement it on Wordpress on a later step

```html
<!DOCTYPE html>
<html lang="de">
<head>
<meta charset="utf-8">
<title>tanu-werk – Ladeinfrastruktur für Elektromobilität</title>
<link rel="stylesheet" href="https://fonts.googleapis.com/css2?family=Audiowide&family=Poppins:wght@400;500;600;700&display=swap">
<style>
:root{
  --pink:#e80a8e;
  --purple:#7a57c9;
  --grad:linear-gradient(90deg,var(--pink),var(--purple));
  --navy:#131a2b;
  --navy-2:#1b2438;
  --ink:#1f2433;
  --white:#ffffff;
  --muted:#d7dbe6;
}
*{box-sizing:border-box;margin:0;padding:0}
html,body{width:1200px;height:3291px;overflow:hidden;background:var(--white)}
body{font-family:"Poppins",sans-serif;color:var(--ink);position:relative}
.page{position:relative;width:1200px;height:3291px}
.abs{position:absolute}
.display{font-family:"Audiowide",sans-serif;font-weight:400}

/* Header */
.site-header{left:0;top:0;width:1200px;height:87px;background:var(--white)}
.brand{left:124px;top:28px;display:flex;align-items:center;gap:10px}
.brand-dot{width:22px;height:22px;border-radius:50%;background:var(--pink)}
.brand-name{font-weight:600;font-size:23px;color:var(--ink);white-space:nowrap}
.nav-item{top:34px;font-size:13.5px;color:var(--ink);white-space:nowrap}
.nav-item.active{border-bottom:2px solid var(--pink);padding-bottom:7px}
.phone-pill{left:880px;top:24px;width:196px;height:38px;border-radius:19px;background:var(--grad);color:var(--white);display:flex;align-items:center;gap:8px;padding-left:6px;font-size:12px;font-weight:600;white-space:nowrap}
.phone-pill .ico{width:28px;height:28px;border-radius:50%;background:var(--white);display:flex;align-items:center;justify-content:center}

/* Hero */
.hero{left:0;top:87px;width:1200px;height:563px;background:linear-gradient(180deg,#4a5566 0%,#6b6560 35%,#5d5348 65%,#3c3d3e 100%)}
.hero-title{left:0;top:130px;width:1200px;text-align:center;color:var(--white);font-size:37px;line-height:51px}
.btn{display:inline-flex;align-items:center;justify-content:center;background:var(--grad);color:var(--white);border-radius:20px;font-weight:600;white-space:nowrap}
.hero-btn{left:491px;top:250px;width:218px;height:40px;font-size:14px}

/* Dark body */
.dark{left:0;top:650px;width:1200px;height:2227px;background:var(--navy)}
.photo{background-color:var(--navy-2)}
.photo-partner{left:0;top:0;width:610px;height:525px;background:radial-gradient(ellipse at 55% 45%,#8a6a4a 0%,#4d4440 35%,#262c3b 65%,var(--navy) 100%)}
.photo-private{left:560px;top:650px;width:560px;height:500px;background:radial-gradient(ellipse at 50% 50%,#7a3538 0%,#4a2e36 35%,#242a3c 65%,var(--navy) 100%)}
.photo-business{left:0;top:1240px;width:645px;height:440px;background:radial-gradient(ellipse at 40% 45%,#5a6d8f 0%,#3a4a68 35%,#222b40 65%,var(--navy) 100%)}
.photo-community{left:540px;top:1690px;width:660px;height:450px;background:radial-gradient(ellipse at 40% 45%,#b8bcc4 0%,#5c6170 30%,#2b3245 62%,var(--navy) 100%)}

.section-title{color:var(--white);font-size:29px;white-space:nowrap}
.copy{color:var(--muted);font-size:13.5px;line-height:21.5px;letter-spacing:.3px}
.partner-title{left:617px;top:76px}
.partner-copy{left:617px;top:122px;width:424px}
.partner-copy p+p{margin-top:16px}
.sec-btn{width:135px;height:37px;font-size:15px}

.ask-title{left:0;top:548px;width:1200px;text-align:center;color:var(--white);font-size:29px;line-height:40px}

.offer-title{color:var(--white);font-size:24px;white-space:nowrap}
.features{list-style:none;color:var(--muted);font-size:13px;line-height:20px}
.features>li{display:flex;gap:14px;margin-bottom:14px}
.features>li:last-child{margin-bottom:0}
.features.compact>li{margin-bottom:8px}
.features.compact>li:first-child{margin-bottom:12px}
.features.tight>li{margin-bottom:13px}
.features.tight>li:last-child{margin-bottom:0}
.features svg{flex:none;margin-top:3px}
.sub-list{list-style:none;margin-top:8px;padding-left:4px}
.sub-list li{display:flex;align-items:center;gap:14px;margin-bottom:5px}
.sub-list li:last-child{margin-bottom:0}
.sub-list li::before{content:"";width:4px;height:4px;border-radius:50%;background:var(--pink)}

/* Footer */
.site-footer{left:0;top:2877px;width:1200px;height:378px;background:var(--white)}
.foot-head{font-family:"Audiowide",sans-serif;font-size:15px;color:var(--ink);white-space:nowrap}
.foot-links{left:162px;list-style:none;font-size:13px}
.foot-links li{margin-bottom:19px}
.contact-list{left:441px;list-style:none;font-size:14px;width:240px}
.contact-list li{display:flex;gap:12px;margin-bottom:20px;line-height:19px}
.c-ico{flex:none;width:34px;height:34px;border-radius:50%;background:var(--grad);display:flex;align-items:center;justify-content:center}
.foot-brand{left:765px;top:166px;width:300px;text-align:center;font-size:34px;line-height:44px;font-weight:600;color:var(--ink);white-space:nowrap}
.socials{left:843px;top:230px;display:flex;gap:17px}
.socials span{width:38px;height:38px;border-radius:50%;background:var(--grad)}
.copyright{left:0;top:3255px;width:1200px;height:36px;background:var(--grad);color:var(--white);font-size:13px;display:flex;align-items:center;justify-content:center}
</style>
</head>
<body>
<div class="page">

<header class="site-header abs">
  <div class="brand abs"><span class="brand-dot"></span><span class="brand-name">tanu-werk.de</span></div>
  <nav class="main-nav">
    <span class="nav-item active abs" style="left:411px">Lösungen</span>
    <span class="nav-item abs" style="left:497px">Unternehmen</span>
    <span class="nav-item abs" style="left:609px">Dienstleistungen</span>
    <span class="nav-item abs" style="left:741px">Karriere</span>
    <span class="nav-item abs" style="left:815px">Kontakt</span>
  </nav>
  <div class="phone-pill abs">
    <span class="ico"><svg width="14" height="14" viewBox="0 0 24 24"><path fill="#e80a8e" d="M6.6 10.8a15 15 0 0 0 6.6 6.6l2.2-2.2c.3-.3.7-.4 1-.2 1.1.4 2.3.6 3.6.6.6 0 1 .4 1 1V20c0 .6-.4 1-1 1A17 17 0 0 1 3 4c0-.6.4-1 1-1h3.5c.6 0 1 .4 1 1 0 1.3.2 2.5.6 3.6.1.3 0 .7-.2 1z"/></svg></span>
    123 456 7890 (Zollfrei)
  </div>
</header>

<section class="hero abs" role="img" aria-label="Foto: weißes Elektroauto an einer Ladesäule vor einem modernen Wohnhaus in der Abenddämmerung">
  <h1 class="hero-title display abs">All-in-One-Lösungen Für Ladeinfrastruktur<br>Für Elektromobilität Anzubieten.</h1>
  <a class="btn hero-btn abs">Kontaktiere Uns Heute</a>
</section>

<main class="dark abs">
  <div class="photo photo-partner abs" role="img" aria-label="Foto: Frau mit Smartphone neben ihrem ladenden Elektroauto bei Sonnenuntergang"></div>
  <h2 class="section-title display partner-title abs">Tanu-werk Ist Ihr Partner</h2>
  <div class="copy partner-copy abs">
    <p>wenn das Laden nicht nur einfach, sondern die Umsetzung auch aus einer Hand kommen soll Wir bieten Lösungen sowohl für Privatkunden, Geschäfts- kunden als auch Kommunen an, die schnell, fair und ohne Eigenleistung zu einer smarten Ladelösung für E-Fahrzeuge kommen möchten.</p>
    <p>Von der Beratung, über die Installation, Inbetriebnahme bis zur Abrechnung und Wartung bekommen Sie bei tanu-werk alles aus einer Hand. Auf Wunsch vermieten wir auch die Ladetechnik und übernehmen im gewerblichen Bereich die direkte Abrechnung mit dem Nutzer.</p>
  </div>
  <a class="btn sec-btn abs" style="left:618px;top:406px">Alle Ansehen</a>

  <h2 class="ask-title display abs">Fragen Sie Uns Nach Der Auf Ihre Individuellen<br>Bedürfnisse Zugeschnittenen Lösung</h2>

  <!-- Privatkunde -->
  <div class="photo photo-private abs" role="img" aria-label="Foto: Frau steckt Ladekabel in ein rotes Elektroauto"></div>
  <h3 class="offer-title display abs" style="left:162px;top:697px">Als Privatkunde</h3>
  <ul class="features abs" style="left:162px;top:748px;width:400px">
    <li><svg width="16" height="14" viewBox="0 0 16 14"><path d="M1 7h4M6 2h4v10H6zM10 4h5M10 10h5" stroke="#b44cc9" stroke-width="1.6" fill="none"/></svg><span>Bestandsanalyse mit umfangreicher Beratung über die Möglichkeiten der Umsetzung</span></li>
    <li><svg width="16" height="14" viewBox="0 0 16 14"><path d="M1 7h4M6 2h4v10H6zM10 4h5M10 10h5" stroke="#b44cc9" stroke-width="1.6" fill="none"/></svg><span>Prüfung und Übernahme der Anmeldung verfügbarer Fördermöglichkeiten</span></li>
    <li><svg width="16" height="14" viewBox="0 0 16 14"><path d="M1 7h4M6 2h4v10H6zM10 4h5M10 10h5" stroke="#b44cc9" stroke-width="1.6" fill="none"/></svg><span>Auswahl an smarten Wallbox Lösungen, passend für Ihr Fahrzeug und Ihre Bedürfnisse</span></li>
    <li><svg width="16" height="14" viewBox="0 0 16 14"><path d="M1 7h4M6 2h4v10H6zM10 4h5M10 10h5" stroke="#b44cc9" stroke-width="1.6" fill="none"/></svg><span>Installation inkl. aller notwendigen Materialien und Tätigkeiten (Durchbrüche, Erdarbeiten, etc.)</span></li>
    <li><svg width="16" height="14" viewBox="0 0 16 14"><path d="M1 7h4M6 2h4v10H6zM10 4h5M10 10h5" stroke="#b44cc9" stroke-width="1.6" fill="none"/></svg><span>Inbetriebnahme und Einweisung in die Ladetechnik</span></li>
    <li><svg width="16" height="14" viewBox="0 0 16 14"><path d="M1 7h4M6 2h4v10H6zM10 4h5M10 10h5" stroke="#b44cc9" stroke-width="1.6" fill="none"/></svg><span>Jährlich technische Wartung nach DGUV3</span></li>
  </ul>
  <a class="btn sec-btn abs" style="left:161px;top:1046px">Alle Ansehen</a>

  <!-- Geschäftskunde -->
  <div class="photo photo-business abs" role="img" aria-label="Foto: blaues Elektroauto mit orangem Ladekabel an einer Wallbox"></div>
  <h3 class="offer-title display abs" style="left:648px;top:1242px">Als Geschäftskunde</h3>
  <ul class="features compact abs" style="left:646px;top:1292px;width:390px">
    <li><svg width="16" height="14" viewBox="0 0 16 14"><path d="M1 7h4M6 2h4v10H6zM10 4h5M10 10h5" stroke="#b44cc9" stroke-width="1.6" fill="none"/></svg><span>Durchführung einer individuellen Bedarfsanalyse inkl. Ermittlung der Anforderungen für:
      <ul class="sub-list">
        <li>Haus- und Immobilienverwaltungen</li>
        <li>Dienstleistungs- und Handelsunternehmen</li>
        <li>Hotel und Beherbergungsbetriebe</li>
        <li>Parkraum- und Parkhausbetreiber</li>
        <li>Tourismus, Sport- und Freizeiteinrichtungen</li>
      </ul></span></li>
    <li><svg width="16" height="14" viewBox="0 0 16 14"><path d="M1 7h4M6 2h4v10H6zM10 4h5M10 10h5" stroke="#b44cc9" stroke-width="1.6" fill="none"/></svg><span>Planung und Projektierung des Installationsaufwands inkl. Materialverbrauch</span></li>
    <li><svg width="16" height="14" viewBox="0 0 16 14"><path d="M1 7h4M6 2h4v10H6zM10 4h5M10 10h5" stroke="#b44cc9" stroke-width="1.6" fill="none"/></svg><span>Leasing oder Kauf der Hardware</span></li>
    <li><svg width="16" height="14" viewBox="0 0 16 14"><path d="M1 7h4M6 2h4v10H6zM10 4h5M10 10h5" stroke="#b44cc9" stroke-width="1.6" fill="none"/></svg><span>Normgerechte Installation der Ladeinfrastruktur inkl. Durchbruch-, Brandschutz- und Erdarbeiten</span></li>
  </ul>
  <a class="btn sec-btn abs" style="left:646px;top:1616px">Alle Ansehen</a>

  <!-- Kommune -->
  <div class="photo photo-community abs" role="img" aria-label="Foto: Reihe von Ladesäulen mit leuchtenden Steckern vor parkenden Autos"></div>
  <h3 class="offer-title display abs" style="left:163px;top:1745px">Als Kommune</h3>
  <ul class="features tight abs" style="left:162px;top:1800px;width:460px">
    <li><svg width="16" height="14" viewBox="0 0 16 14"><path d="M1 7h4M6 2h4v10H6zM10 4h5M10 10h5" stroke="#b44cc9" stroke-width="1.6" fill="none"/></svg><span>Konzeptionierung möglicher Ladeinfrastrukturen innerhalb<br>Ihrer Gemeinde</span></li>
    <li><svg width="16" height="14" viewBox="0 0 16 14"><path d="M1 7h4M6 2h4v10H6zM10 4h5M10 10h5" stroke="#b44cc9" stroke-width="1.6" fill="none"/></svg><span>Planung und Projektsteuerung inkl. sämtlicher behördlicher Genehmigungsverfahren und Beantragung von Fördermitteln</span></li>
    <li><svg width="16" height="14" viewBox="0 0 16 14"><path d="M1 7h4M6 2h4v10H6zM10 4h5M10 10h5" stroke="#b44cc9" stroke-width="1.6" fill="none"/></svg><span>Fachgerechte Installation und Inbetriebnahme</span></li>
    <li><svg width="16" height="14" viewBox="0 0 16 14"><path d="M1 7h4M6 2h4v10H6zM10 4h5M10 10h5" stroke="#b44cc9" stroke-width="1.6" fill="none"/></svg><span>Regelmäßige Wartung gemäß Vorschrif</span></li>
    <li><svg width="16" height="14" viewBox="0 0 16 14"><path d="M1 7h4M6 2h4v10H6zM10 4h5M10 10h5" stroke="#b44cc9" stroke-width="1.6" fill="none"/></svg><span>Reparatur und Kundenservice</span></li>
    <li><svg width="16" height="14" viewBox="0 0 16 14"><path d="M1 7h4M6 2h4v10H6zM10 4h5M10 10h5" stroke="#b44cc9" stroke-width="1.6" fill="none"/></svg><span>Direkte Abrechnung mit dem Nutzer</span></li>
    <li><svg width="16" height="14" viewBox="0 0 16 14"><path d="M1 7h4M6 2h4v10H6zM10 4h5M10 10h5" stroke="#b44cc9" stroke-width="1.6" fill="none"/></svg><span>Beteiligung der Gemeinde am Umsatz</span></li>
  </ul>
  <a class="btn sec-btn abs" style="left:161px;top:2078px">Alle Ansehen</a>
</main>

<footer class="site-footer abs">
  <h4 class="foot-head abs" style="left:162px;top:80px">Schnelle Links</h4>
  <ul class="foot-links abs" style="top:118px">
    <li>AGB</li><li>Datenschutzerklärung</li><li>Impressum</li><li>Kontakt</li><li>Karriere</li><li>FAQs</li>
  </ul>
  <h4 class="foot-head abs" style="left:441px;top:80px">Kontaktangaben</h4>
  <ul class="contact-list abs" style="top:118px">
    <li><span class="c-ico"><svg width="14" height="16" viewBox="0 0 14 18"><path fill="#fff" d="M7 0a7 7 0 0 0-7 7c0 5 7 11 7 11s7-6 7-11a7 7 0 0 0-7-7zm0 9.5A2.5 2.5 0 1 1 7 4.5a2.5 2.5 0 0 1 0 5z"/></svg></span><span><span style="font-size:16px">Ein Kleid</span><br><span style="font-size:13px">12 Gebäude, Straße, Stadt, Bundesland</span></span></li>
    <li><span class="c-ico"><svg width="14" height="14" viewBox="0 0 24 24"><path fill="#fff" d="M6.6 10.8a15 15 0 0 0 6.6 6.6l2.2-2.2c.3-.3.7-.4 1-.2 1.1.4 2.3.6 3.6.6.6 0 1 .4 1 1V20c0 .6-.4 1-1 1A17 17 0 0 1 3 4c0-.6.4-1 1-1h3.5c.6 0 1 .4 1 1 0 1.3.2 2.5.6 3.6.1.3 0 .7-.2 1z"/></svg></span><span style="padding-top:2px">123 456 7890 (Zollfrei)</span></li>
    <li><span class="c-ico"><svg width="15" height="12" viewBox="0 0 20 14"><rect width="20" height="14" rx="2" fill="#fff"/><path d="M1 1l9 7 9-7" stroke="#b44cc9" stroke-width="1.6" fill="none"/></svg></span><span style="padding-top:8px">info@tanu-werk.de</span></li>
  </ul>
  <div class="foot-brand abs">tanu-werk.de</div>
  <div class="socials abs" aria-label="Soziale Netzwerke"><span></span><span></span><span></span></div>
</footer>

<div class="copyright abs">Urheberrecht © 2022 tanu-werk.de. Alle Rechte vorbehalten.</div>

</div>
</body>
</html>
```